Need a Basketball Court Design

We are replacing our current basketball court (gym floor) and we are looking for a new design. Our team is the “Larkmoor Falcons”. Our mascot is a “Knight” (in shining armor). Our colors are royal blue/grey/black. We are looking for a design that is contemporary and energetic.
The background of the court should display a “castle”. In the center of the court should be a team logo. You can use one of our existing logos or create your own. Along the baseline of the court should read the word “Larkmoor”.
I’ve attached ...
1) a picture of the current court
2) a mock-up design of what we are thinking
3) some of the different team logos we use.

```html
<!DOCTYPE html>
<html lang="en">
<head>
<meta charset="utf-8">
<title>Larkmoor Falcons Court Design</title>
<link rel="stylesheet" href="https://fonts.googleapis.com/css2?family=Graduate&display=swap">
<style>
  :root {
    --royal: #274b93;
    --ink: #050505;
    --line: #ffffff;
    --maple-light: #ecc998;
    --maple-mid: #e2b47a;
    --maple-deep: #d6a266;
    --page: #ffffff;
  }
  html, body {
    margin: 0;
    padding: 0;
    width: 1200px;
    height: 600px;
    overflow: hidden;
    background: var(--page);
  }
  .court-design {
    display: block;
    width: 1200px;
    height: 600px;
  }
  .frame-band { fill: var(--royal); }
  .boundary { fill: none; stroke: var(--line); stroke-width: 3; }
  .court-line { fill: none; stroke: var(--line); stroke-width: 2.5; }
  .paint { fill: var(--ink); }
  .paint-disc { fill: var(--royal); stroke: var(--line); stroke-width: 2; }
  .hash { stroke: var(--line); stroke-width: 1.5; }
  .side-word {
    font-family: "Graduate", serif;
    font-size: 62px;
    fill: var(--ink);
    stroke: var(--line);
    stroke-width: 3;
    paint-order: stroke fill;
  }
  .welcome-line {
    font-family: "Graduate", serif;
    font-size: 32px;
    fill: var(--line);
  }
  .team-mark {
    font-family: "Graduate", serif;
    fill: var(--royal);
  }
  .team-mark-small { font-size: 26px; }
  .team-mark-center { font-size: 54px; }
</style>
</head>
<body>
<svg class="court-design" viewBox="0 0 1200 600" xmlns="http://www.w3.org/2000/svg" role="img" aria-label="Larkmoor Falcons basketball court floor design">
  <defs>
    <linearGradient id="maple-floor" x1="0" y1="0" x2="1" y2="1">
      <stop offset="0" stop-color="#ecc998"/>
      <stop offset="0.5" stop-color="#e2b47a"/>
      <stop offset="1" stop-color="#d6a266"/>
    </linearGradient>
  </defs>

  <rect class="frame-band" x="67" y="13" width="1077" height="574"/>

  <rect x="134" y="50" width="940" height="498" fill="url(#maple-floor)" role="img" aria-label="Light maple hardwood floor planks"/>
  <rect class="boundary" x="134" y="50" width="940" height="498"/>
  <line class="court-line" x1="605" y1="50" x2="605" y2="548"/>

  <g class="court-end court-end-left">
    <path class="court-line" d="M136 101 H190 A197 197 0 0 1 190 495 H136"/>
    <rect class="paint" x="136" y="238" width="177" height="119"/>
    <path class="paint-disc" d="M313 238 A60 60 0 0 0 313 357 Z"/>
    <path class="court-line" d="M313 238 A60 60 0 0 1 313 357"/>
    <line class="court-line" x1="166" y1="262" x2="166" y2="333"/>
    <line class="court-line" x1="166" y1="297" x2="170" y2="297"/>
    <circle class="court-line" cx="187" cy="297" r="17"/>
    <g class="hash">
      <line x1="200" y1="232" x2="200" y2="238"/><line x1="228" y1="232" x2="228" y2="238"/>
      <line x1="257" y1="232" x2="257" y2="238"/><line x1="286" y1="232" x2="286" y2="238"/>
      <line x1="200" y1="357" x2="200" y2="363"/><line x1="228" y1="357" x2="228" y2="363"/>
      <line x1="257" y1="357" x2="257" y2="363"/><line x1="286" y1="357" x2="286" y2="363"/>
    </g>
  </g>

  <g class="court-end court-end-right" transform="translate(1208 0) scale(-1 1)">
    <path class="court-line" d="M136 101 H190 A197 197 0 0 1 190 495 H136"/>
    <rect class="paint" x="136" y="238" width="177" height="119"/>
    <path class="paint-disc" d="M313 238 A60 60 0 0 0 313 357 Z"/>
    <path class="court-line" d="M313 238 A60 60 0 0 1 313 357"/>
    <line class="court-line" x1="166" y1="262" x2="166" y2="333"/>
    <line class="court-line" x1="166" y1="297" x2="170" y2="297"/>
    <circle class="court-line" cx="187" cy="297" r="17"/>
    <g class="hash">
      <line x1="200" y1="232" x2="200" y2="238"/><line x1="228" y1="232" x2="228" y2="238"/>
      <line x1="257" y1="232" x2="257" y2="238"/><line x1="286" y1="232" x2="286" y2="238"/>
      <line x1="200" y1="357" x2="200" y2="363"/><line x1="228" y1="357" x2="228" y2="363"/>
      <line x1="257" y1="357" x2="257" y2="363"/><line x1="286" y1="357" x2="286" y2="363"/>
    </g>
  </g>

  <g class="team-mark team-mark-small" text-anchor="middle">
    <text x="437" y="150">LARKMOOR</text>
    <text x="437" y="182">FALCONS</text>
  </g>
  <text class="team-mark team-mark-center" x="605" y="318" text-anchor="middle" textLength="330" lengthAdjust="spacingAndGlyphs">LARKMOOR</text>
  <g class="team-mark team-mark-small" text-anchor="middle" transform="rotate(180 771 450)">
    <text x="771" y="440">LARKMOOR</text>
    <text x="771" y="472">FALCONS</text>
  </g>

  <text class="side-word" x="101" y="292" text-anchor="middle" dominant-baseline="central" textLength="295" lengthAdjust="spacingAndGlyphs" transform="rotate(-90 101 292)">FALCONS</text>
  <text class="side-word" x="1108" y="295" text-anchor="middle" dominant-baseline="central" textLength="440" lengthAdjust="spacingAndGlyphs" transform="rotate(90 1108 295)">BASKETBALL</text>
  <text class="welcome-line" x="615" y="580" text-anchor="middle" textLength="586" lengthAdjust="spacingAndGlyphs">WELCOME TO THE FALCON NEST</text>
</svg>
</body>
</html>
```